Vorn upkeep KT Solar Venture

Solar power system install
Services and maintenance
wiring, Rewinding and Renovation
Switch Board Upgrade
Power and lighting point
t doesn’t matter how much you spend on quality parts, your solar system will let you down if your design and installation are sub-par. Have your solar system tailored and installed by our Master Electrician and Bright Grid Guild Accredited team.

Target Market(s)

sales and installed

Industry/Entity Type

Solar install and retailer

Contact Information for Business Card

Name , Email, Phone Number ,Business address,

Font styles to use
Serif

Colors
0054AA
0677BA
7BADD7
CADEEF
E8F1F8

Requirements
Must have
• clear and bright
Nice to have
• new design
Should not have
• unclear pictures

```html
<!DOCTYPE html>
<html lang="en">
<head>
<meta charset="utf-8">
<title>Vorn upkeep – Business Card</title>
<link href="https://fonts.googleapis.com/css2?family=Roboto:wght@400;500;700;900&display=swap" rel="stylesheet">
<style>
  :root {
    --backdrop: #2e2e2e;
    --card: #f1f1f1;
    --brand-blue: #0054AA;
    --band-blue: #0677BA;
    --band-green: #6aab35;
    --accent-green: #3f9a35;
    --ink: #1e1e1e;
    --band-text: #eef6ee;
  }
  * { box-sizing: border-box; margin: 0; padding: 0; }
  html, body { width: 1200px; height: 1138px; overflow: hidden; }
  body {
    background: var(--backdrop);
    font-family: "Roboto", Arial, sans-serif;
    position: relative;
  }
  .card {
    position: absolute;
    background: linear-gradient(180deg, #f6f6f6 0%, #e9e9e9 100%);
    border-radius: 16px;
    overflow: hidden;
  }
  .card--front { left: 274px; top: 186px; width: 623px; height: 376px; }
  .card--back  { left: 276px; top: 608px; width: 618px; height: 374px; }

  .brand-mark {
    position: absolute;
    border-radius: 50%;
    background: var(--brand-blue);
  }
  .brand-name {
    position: absolute;
    color: var(--brand-blue);
    font-weight: 900;
    text-transform: uppercase;
    letter-spacing: 0.5px;
    line-height: 1.08;
  }
  .card--front .brand-mark { left: 130px; top: 84px; width: 66px; height: 66px; }
  .card--front .brand-name { left: 222px; top: 80px; font-size: 33px; }

  .service-band {
    position: absolute;
    left: 0; top: 239px; width: 100%; height: 74px;
    background: linear-gradient(90deg, var(--band-green) 0%, #3e9a6a 40%, var(--band-blue) 72%, var(--band-blue) 100%);
    color: var(--band-text);
    font-size: 15.5px;
    text-align: center;
    padding-top: 11px;
    line-height: 23px;
  }
  .web-row {
    position: absolute;
    left: 0; top: 331px; width: 100%;
    display: flex; justify-content: center; align-items: center; gap: 26px;
    font-size: 15.5px; color: var(--ink);
  }
  .web-row .rule { width: 80px; height: 2px; }
  .web-row .rule--blue { background: linear-gradient(90deg, transparent, var(--band-blue)); }
  .web-row .rule--green { background: linear-gradient(90deg, var(--band-green), transparent); }

  .card--back .brand-mark { left: 118px; top: 94px; width: 78px; height: 78px; }
  .card--back .brand-name { left: 0; width: 316px; top: 186px; font-size: 26px; text-align: center; }

  .contact { position: absolute; left: 344px; top: 75px; color: var(--ink); }
  .contact__name { color: var(--brand-blue); font-size: 25px; font-weight: 500; }
  .contact__role { font-size: 16px; margin-top: 6px; }
  .contact__address { font-size: 16px; line-height: 24px; margin-top: 24px; }
  .contact__list { list-style: none; margin-top: 8px; font-size: 16px; line-height: 24px; }
  .contact__list li { display: flex; align-items: center; gap: 14px; }
  .contact__list svg { width: 17px; height: 14px; fill: var(--accent-green); }

  .footer-bar { position: absolute; left: 0; bottom: 0; width: 618px; height: 48px; }
  .footer-bar__text {
    position: absolute; left: 344px; bottom: 17px;
    color: #eaf2fa; font-size: 16px;
  }
</style>
</head>
<body>
  <section class="card card--front">
    <div class="brand-mark"></div>
    <div class="brand-name">Vorn upkeep<br>KT Solar Venture</div>
    <div class="service-band">
      Solar Power System Install &nbsp;|&nbsp; Wiring, Rewinding &amp; Renovation<br>
      Services &amp; Maintenance &nbsp;|&nbsp; Switch Board Upgrade &nbsp;|&nbsp; Power &amp; Lighting Point
    </div>
    <div class="web-row">
      <span class="rule rule--blue"></span>
      <span>www.ktsolarventure.com</span>
      <span class="rule rule--green"></span>
    </div>
  </section>

  <section class="card card--back">
    <div class="brand-mark"></div>
    <div class="brand-name">Vorn upkeep<br>KT Solar Venture</div>
    <div class="contact">
      <div class="contact__name">John Doe Smith</div>
      <div class="contact__role">Managing Director</div>
      <div class="contact__address">234 Anywhere St., Any City,<br>Any Town, US 123456</div>
      <ul class="contact__list">
        <li><svg viewBox="0 0 17 14" aria-hidden="true"><path d="M2 4c0-2 3-3 6.5-3S15 2 15 4l-3 1-1-2H6L5 5zM4 6h9l2 7H2z"/></svg>828-111-1111</li>
        <li><svg viewBox="0 0 17 14" aria-hidden="true"><path d="M1 2h15v10H1zM2 3l6.5 5L15 3v1L8.5 9 2 4z" fill-rule="evenodd"/></svg>john@yourwebsite.com</li>
        <li><svg viewBox="0 0 17 14" aria-hidden="true"><circle cx="8.5" cy="7" r="6"/><path d="M2.5 7h12M8.5 1v12M5 2c2 3 2 7 0 10M12 2c-2 3-2 7 0 10" stroke="#f1f1f1" stroke-width="0.9" fill="none"/></svg>www.yourwebsite.com</li>
      </ul>
    </div>
    <svg class="footer-bar" viewBox="0 0 618 48" preserveAspectRatio="none" aria-hidden="true">
      <defs>
        <linearGradient id="stripGreen" x1="0" x2="1">
          <stop offset="0" stop-color="#7dbb3a"/>
          <stop offset="1" stop-color="#2f9a3a"/>
        </linearGradient>
      </defs>
      <rect x="0" y="33" width="360" height="15" fill="url(#stripGreen)"/>
      <path d="M292 0H618V48H266L282 10Q286 0 292 0Z" fill="#0a6aad"/>
    </svg>
    <div class="footer-bar__text">Solar power system install</div>
  </section>
</body>
</html>
```